Management Consultancy needs sharp professional services showcased in a brochure

We are a management consultancy specializing on contract management and conflict avoidance services requiring a professional brochure showcasing our services to prospective clients.

Attached are a selection of existing stationary and the colour scheme.

Further details on our company can be found at www.velt-advisory-partners.com
Updates

Preference is for bi-fold, however, innovative tri-fold will be considered. Added Monday, August 7, 2017

Target Market(s)

Construction companies, consultants, developers, oil and gas service providers, NGO's, SME's.

Industry/Entity Type

Management

Requirements
Must have
• High degree of professionalism with eye catching, sharp detail. No frils.
• Colour scheme as per the attachments
• Font as per attachments - Century Gothic
• Details of our company and services
Nice to have
• Open to ideas, thinking along the lines of a car brochure type design.
• Bi-fold preferred, by trifold accepted if innovative.
Should not have
• Remove reference to the United Arab Emirates.
• No cartoon/clipart photos.

```html
<!DOCTYPE html>
<html lang="en">
<head>
<meta charset="utf-8">
<title>Velt Advisory – Contract &amp; Conflict Advisory Brochure</title>
<link rel="stylesheet" href="https://fonts.googleapis.com/css2?family=Marcellus+SC&family=Questrial&display=swap">
<style>
  :root{
    --red:#c4161c;
    --red-deep:#9e0f14;
    --navy:#253f63;
    --navy-deep:#1b2f4b;
    --ink:#4a4a4a;
    --paper:#ffffff;
    --stage:#e8e8ea;
  }
  *{box-sizing:border-box;margin:0;padding:0}
  html,body{width:1200px;height:1200px;overflow:hidden;background:var(--stage)}
  body{font-family:"Questrial",sans-serif;color:var(--ink);position:relative}
  .spread{position:absolute;left:204px;width:792px;height:560px;background:var(--paper);box-shadow:0 6px 18px rgba(0,0,0,.18);overflow:hidden}
  .spread--outer{top:30px}
  .spread--inner{top:610px}
  .spread__spine{position:absolute;left:395px;top:0;width:2px;height:100%;background:linear-gradient(90deg,rgba(0,0,0,.07),rgba(0,0,0,0));z-index:5}
  .spread__art{position:absolute;inset:0;width:792px;height:560px}
  .page{position:absolute;top:0;width:396px;height:560px}
  .page--left{left:0}
  .page--right{left:396px}

  .heading{font-family:"Marcellus SC",serif;color:var(--red);font-size:20px;letter-spacing:.5px;line-height:1}
  .subheading{font-size:10px;font-weight:bold;color:var(--navy);margin:3px 0 3px}
  .service-list{list-style:none;font-size:7.5px;line-height:1.45;color:var(--ink)}
  .service-list li::before{content:"";display:inline-block;width:3px;height:3px;border-radius:50%;background:var(--red);margin-right:5px;vertical-align:middle}

  .services{position:absolute;top:38px;left:26px;width:360px;display:flex;gap:30px}
  .services__col{flex:1}

  .brand{display:flex;align-items:center;gap:6px;font-family:"Questrial",sans-serif;font-size:17px;color:var(--navy);letter-spacing:.5px}
  .brand__dot{width:12px;height:12px;border-radius:50%;background:var(--red)}
  .brand--light{color:#fff;font-size:14px}
  .brand--light .brand__dot{background:#fff}

  .contact{position:absolute;left:236px;top:345px;color:#fff}
  .contact__list{list-style:none;margin-top:8px;font-size:9px;line-height:1.75}
  .contact__list li{display:flex;align-items:center;gap:6px}
  .contact__list svg{width:8px;height:8px;fill:#fff;flex:none}

  .cover-brand{position:absolute;top:42px;left:0;width:396px;display:flex;justify-content:center}
  .cover-title{position:absolute;top:122px;left:30px;width:350px;text-align:center;font-family:"Marcellus SC",serif;color:#fff;font-size:23px;line-height:1.3;letter-spacing:.5px}

  .about{position:absolute;left:24px;top:222px;width:350px}
  .about .heading{color:var(--navy);font-size:19px}
  .about__intro{font-size:7px;line-height:1.35;margin-top:5px}
  .sectors{position:relative;height:118px;margin-top:8px}
  .sector{position:absolute;width:128px;height:22px;border-radius:5px;background:var(--navy);color:#fff;font-size:7px;display:flex;align-items:center;justify-content:center;text-align:center;line-height:1.1;padding:0 6px}
  .sector__icon{position:absolute;top:-19px;left:50%;margin-left:-9px;width:18px;height:18px;border-radius:50%;background:var(--red);border:2px solid #fff;display:flex;align-items:center;justify-content:center}
  .sector__icon svg{width:8px;height:8px;fill:#fff}
  .body-copy{font-size:7px;line-height:1.4;margin-top:6px}
  .body-copy strong{color:var(--red);font-weight:bold}
  .body-copy b{color:var(--navy)}

  .about-right{position:absolute;left:22px;top:200px;width:350px}
  .quote{margin-top:12px;font-family:"Marcellus SC",serif;font-size:9px;color:var(--navy);line-height:1.3;padding:0 20px;position:relative}
  .quote::before,.quote::after{font-family:serif;color:var(--red);font-size:20px;position:absolute;line-height:1}
  .quote::before{content:"\201C";left:2px;top:0}
  .quote::after{content:"\201D";right:30px;bottom:-8px}
  .inner-brand{position:absolute;left:100px;top:470px}
</style>
</head>
<body>

<section class="spread spread--outer">
  <svg class="spread__art" viewBox="0 0 792 560">
    <defs>
      <linearGradient id="redFade" x1="0" y1="0" x2="1" y2="1">
        <stop offset="0" stop-color="#d21c22"/>
        <stop offset="1" stop-color="#a90f15"/>
      </linearGradient>
      <linearGradient id="officePhoto" x1="0" y1="0" x2="1" y2="1">
        <stop offset="0" stop-color="#dfe6ee"/>
        <stop offset=".55" stop-color="#b7c3cf"/>
        <stop offset="1" stop-color="#3a4252"/>
      </linearGradient>
      <linearGradient id="portraitPhoto" x1="0" y1="0" x2="0" y2="1">
        <stop offset="0" stop-color="#eef0f3"/>
        <stop offset=".45" stop-color="#c8b2a0"/>
        <stop offset="1" stop-color="#262b36"/>
      </linearGradient>
    </defs>
    <path d="M396,92 C300,118 215,230 176,560 L160,560 C200,225 290,108 396,84 Z" fill="var(--navy)"/>
    <path d="M396,100 C305,126 225,240 190,560 L396,560 Z" fill="url(#redFade)"/>
    <path role="img" aria-label="Photo: smiling young consultant in a dark suit giving a thumbs up" d="M20,560 L20,340 Q60,290 120,290 Q175,300 190,350 L176,560 Z" fill="url(#portraitPhoto)"/>
    <path d="M396,92 L792,88 L792,228 C640,236 520,310 482,560 L396,560 Z" fill="url(#redFade)"/>
    <path d="M792,236 C650,244 535,318 500,560 L492,560 C528,312 646,240 792,230 Z" fill="#fff"/>
    <path role="img" aria-label="Photo: business people shaking hands across a meeting table" d="M792,246 C660,254 548,326 512,560 L792,560 Z" fill="url(#officePhoto)"/>
  </svg>
  <div class="spread__spine"></div>

  <div class="page page--left">
    <div class="services">
      <div class="services__col">
        <h2 class="heading">Our Services</h2>
        <h3 class="subheading">Conflict Advisory</h3>
        <ul class="service-list">
          <li>Restoration and Mediation Services</li>
          <li>Shuttle Diplomacy Services and In Person</li>
          <li>Intermediary Services</li>
          <li>Negotiation Support Services</li>
          <li>Workplace Mediation Services</li>
        </ul>
      </div>
      <div class="services__col">
        <h3 class="subheading">Contract Advisory</h3>
        <ul class="service-list">
          <li>Contract Troubleshooting</li>
          <li>Contracts Audit Services and Performance Management</li>
          <li>Strategic Review &amp; Risk Assessment</li>
          <li>Contract Fraud Investigation</li>
        </ul>
      </div>
    </div>

    <div class="contact">
      <div class="brand brand--light"><span class="brand__dot"></span>Velt Advisory</div>
      <ul class="contact__list">
        <li><svg viewBox="0 0 10 10"><path d="M2 0h2l1 3-1.5 1a6 6 0 0 0 2.5 2.5L7 5l3 1v2a2 2 0 0 1-2 2A8 8 0 0 1 0 2a2 2 0 0 1 2-2z"/></svg>your ph no. goes here</li>
        <li><svg viewBox="0 0 10 10"><path d="M0 2h10v6H0zM0 2l5 3.5L10 2" stroke="#c4161c" stroke-width=".6"/></svg>your mail address goes here</li>
        <li><svg viewBox="0 0 10 10"><circle cx="5" cy="5" r="4.5"/></svg>www.velt-advisory-partners.com</li>
        <li><svg viewBox="0 0 10 10"><path d="M5 0a3.5 3.5 0 0 1 3.5 3.5C8.5 6 5 10 5 10S1.5 6 1.5 3.5A3.5 3.5 0 0 1 5 0z"/></svg>your address goes here</li>
      </ul>
    </div>
  </div>

  <div class="page page--right">
    <div class="cover-brand"><div class="brand"><span class="brand__dot"></span>Velt Advisory</div></div>
    <h1 class="cover-title">The Contract &amp;<br>Conflict Advisory</h1>
  </div>
</section>

<section class="spread spread--inner">
  <svg class="spread__art" viewBox="0 0 792 560">
    <defs>
      <linearGradient id="deskPhoto" x1="0" y1="0" x2="1" y2="0">
        <stop offset="0" stop-color="#eef1f4"/>
        <stop offset=".6" stop-color="#cdd5de"/>
        <stop offset="1" stop-color="#2c3444"/>
      </linearGradient>
    </defs>
    <path role="img" aria-label="Photo: hands signing a contract beside financial charts and a calculator" d="M0,0 H792 V118 C600,168 360,196 0,96 Z" fill="url(#deskPhoto)"/>
    <path d="M0,96 C360,196 600,168 792,118 V132 C600,190 360,214 0,140 Z" fill="var(--red)"/>
    <path d="M0,140 C360,214 600,190 792,132 V136 C600,198 360,226 0,150 Z" fill="var(--red-deep)" opacity=".55"/>
    <path d="M792,400 C700,410 630,470 600,560 L640,560 C668,482 726,432 792,424 Z" fill="var(--navy)"/>
    <path d="M792,440 C730,450 690,500 676,560 L700,560 C714,510 748,470 792,462 Z" fill="var(--navy-deep)"/>
  </svg>
  <div class="spread__spine"></div>

  <div class="page page--left">
    <div class="about">
      <h2 class="heading">About Us</h2>
      <p class="about__intro">We are an experienced contract and conflict advisory providing global contract performance solutions and conflict management to:</p>
      <div class="sectors">
        <div class="sector" style="left:28px;top:30px"><span class="sector__icon"><svg viewBox="0 0 10 10"><circle cx="5" cy="5" r="4"/></svg></span>International development organisations</div>
        <div class="sector" style="left:200px;top:18px"><span class="sector__icon"><svg viewBox="0 0 10 10"><path d="M1 9V4l4-3 4 3v5z"/></svg></span>Construction industry</div>
        <div class="sector" style="left:210px;top:72px"><span class="sector__icon"><svg viewBox="0 0 10 10"><path d="M0 3l5-3 5 3zM1 4h1v4H1zm3 0h2v4H4zm4 0h1v4H8zM0 9h10v1H0z"/></svg></span>Government sectors</div>
        <div class="sector" style="left:36px;top:88px"><span class="sector__icon"><svg viewBox="0 0 10 10"><path d="M5 0C3 4 2 5 2 7a3 3 0 0 0 6 0c0-2-1-3-3-7z"/></svg></span>Oil and gas industry</div>
      </div>
      <p class="body-copy">Observing the standard of consultancy services and magnitude of contractual engagements and conflicts, we see the opportunity to make things better, <strong>better engagements, better awareness, better performance</strong>, which all lead to <strong>better value</strong> in terms of financial benefit and relationship maintenance. We firmly believe in party success in a non litigious environment.</p>
      <p class="body-copy">Our services are uniquely delivered through our integrated management consultancy model, with a single point of contact and responsibility, and focused attention to detail. We provide <strong>advisory services and solutions resolving past and current claims, and in doing so, preparing our clients for a conflict free future</strong> based on our core principles of integrity, equality and strength, ensuring compliance and experience at an intimate professional level. We aim to have our clients feel our principles in our presence and in our advisories, giving the service which is deserved.</p>
      <p class="body-copy">Our clients range from <b>global Top Tier 500 companies</b>, international contractors to government bodies and authorities.</p>
    </div>
  </div>

  <div class="page page--right">
    <div class="about-right">
      <p class="body-copy">Velt Advisory is more than just a professional advisory consultancy; we are an integrated professional team with deep domain expertise, industry knowledge and the ability to work across multiple jurisdictions supported by a wide professional network.</p>
      <p class="body-copy">We <strong>forge strong client partnerships</strong> and in doing so, we develop and maintain these relationships through performance and delivery of professional services which <strong>create and maximise value for our clients.</strong></p>
      <p class="body-copy">Through our unique approach to contract and conflict management, we want the best for our clients to ensure that contract integrity, compliance and performance is maintained with the upmost faith, based around our principles.</p>
      <p class="quote">If value, whether financial or relationship is not achieved, then we are not finished. We have only just begun.</p>
    </div>
    <div class="inner-brand"><div class="brand"><span class="brand__dot"></span>Velt Advisory</div></div>
  </div>
</section>

</body>
</html>
```